Business Card for Polygraph business in Africa

Business Card . Polygraph Examiner based in Tanzania, East Africa.
Business Card will be used to disseminate contact information to potential clients.
It should convey that I am a professional specifically in the polygraph field and perform my work with integrity.

I have attached the business card that I'm currently using, which I threw together myself initially. It's not professional enough.

Target Market(s)

Banks, Accounting Firms, Government Ministries, Gas, Oil, & Gemstone Mining Concerns, Wildlife Conservation NGOs, International companies located in East Africa.

Industry/Entity Type

Business

Contact Information for Business Card

Veritrace Kilonga
Miriam Holloway
PO Box 48317
Arusha, Tanzania
+255 612 839 274
miriamholloway@postvale.example

Colors
00a990
f37122
faa54b

Requirements
Must have
• - Veritrace Kilonga (with the word "Polygraph" being more prominent than the word "Tanzania")
• - Forensic Examinations
• - Employment Screening
• - Should contain a logo of the Continental Truthline Society (of which I'm a member)
• - I would like an accent design (such as the polygraph "squiggles" of a cardio tracing or such as that)
• - My contact information (less prominent, but large enough to read legibly). I would also consider putting the contact information on the second side of the card.
Nice to have
• My color suggestions are changeable.
Should not have
• Anything "cutesy" or "cartoonish"

```html
<!DOCTYPE html>
<html lang="en">
<head>
<meta charset="utf-8">
<title>Veritrace Kilonga – Business Card</title>
<link href="https://fonts.googleapis.com/css2?family=Roboto:wght@400&family=Roboto+Condensed:wght@700&family=Didact+Gothic&display=swap" rel="stylesheet">
<style>
  :root{
    --backdrop:#2b2b2b;
    --brand-blue:#0b4a9e;
    --card-white:#f1f1f1;
    --text-grey:#5f5f5f;
    --rule-grey:#8a8a8a;
    --white:#ffffff;
  }
  *{margin:0;padding:0;box-sizing:border-box}
  html,body{width:1200px;height:960px;overflow:hidden;background:var(--backdrop)}
  .canvas{position:relative;width:1200px;height:960px}
  .card{position:absolute;left:320px;width:600px;height:342px;border-radius:18px}
  .card-front{top:108px;background:var(--brand-blue);color:var(--white)}
  .card-back{top:493px;background:var(--card-white)}

  .front-mark{position:absolute;left:0;right:0;top:148px;text-align:center;
    font-family:"Roboto",sans-serif;font-weight:400;font-size:36px;letter-spacing:1px;color:var(--white)}
  .front-tagline{position:absolute;left:0;right:0;top:287px;text-align:center;
    font-family:"Roboto",sans-serif;font-size:15px;color:var(--white)}
  .front-tagline .dot{display:inline-block;width:7px;height:7px;border-radius:50%;
    background:var(--white);margin:0 7px 1px 9px;vertical-align:middle}

  .back-mark{position:absolute;right:36px;top:38px;text-align:right}
  .back-mark .name{font-family:"Roboto Condensed",sans-serif;font-weight:700;font-size:21px;
    color:var(--brand-blue);letter-spacing:.5px;text-transform:uppercase;line-height:1}
  .back-mark .tagline{margin-top:5px;padding-top:3px;border-top:1px solid var(--brand-blue);
    font-family:"Roboto",sans-serif;font-size:8.5px;color:var(--text-grey);text-transform:uppercase;letter-spacing:.3px}

  .member-badge{position:absolute;left:498px;top:99px;width:66px;height:66px;border-radius:50%;
    border:3px solid #2f3a8f;background:var(--white)}

  .contact-icons{position:absolute;left:28px;top:160px;width:20px}
  .divider{position:absolute;left:65px;top:158px;width:1px;height:154px;background:var(--rule-grey)}
  .contact{position:absolute;left:84px;top:156px;font-family:"Didact Gothic",sans-serif;color:var(--text-grey)}
  .contact .person{font-family:"Roboto Condensed",sans-serif;font-weight:700;font-size:22px;color:var(--brand-blue);text-transform:uppercase;line-height:26px}
  .contact .company{font-family:"Roboto Condensed",sans-serif;font-weight:700;font-size:15px;color:var(--text-grey);text-transform:uppercase;letter-spacing:.5px;line-height:20px}
  .contact .line{font-size:15px;line-height:19px}
  .contact .address{margin-top:8px}
  .contact .reach{margin-top:8px}
</style>
</head>
<body>
<div class="canvas">
  <section class="card card-front">
    <div class="front-mark">Veritrace Kilonga</div>
    <div class="front-tagline">Forensic Examinations<span class="dot"></span>Employment Screening</div>
  </section>

  <section class="card card-back">
    <div class="back-mark">
      <div class="name">Veritrace Kilonga</div>
      <div class="tagline">Forensic Examinations • Employment Screening</div>
    </div>
    <div class="member-badge" role="img" aria-label="Continental Truthline Society membership seal"></div>

    <svg class="contact-icons" width="20" height="150" viewBox="0 0 20 150" fill="#0b4a9e" aria-hidden="true">
      <circle cx="10" cy="5" r="4.5"/>
      <path d="M2 16c0-5 4-6 8-6s8 1 8 6z"/>
      <path d="M10 50c-3.3 0-6 2.6-6 6 0 4.5 6 10 6 10s6-5.5 6-10c0-3.4-2.7-6-6-6zm0 8.5a2.5 2.5 0 1 1 0-5 2.5 2.5 0 0 1 0 5z"/>
      <path d="M5 90c1-1 2.5-1 3 0l1.5 2.5c.4.8 0 1.6-.6 2l-1 .8c.8 1.8 2.2 3.2 4 4l.8-1c.4-.6 1.2-1 2-.6L17 99c1 .5 1 2 0 3l-1.2 1c-5 1-11.8-5.8-10.8-10.8z"/>
      <rect x="4" y="112" width="12" height="8" rx="1"/>
      <path d="M4.5 112.8l5.5 4 5.5-4" fill="none" stroke="#f1f1f1" stroke-width="1.2"/>
      <circle cx="10" cy="134" r="6"/>
      <path d="M7 131c2 0 2 2 4 2s1 3 3 3M8 137c1-1 2 0 3 1" fill="none" stroke="#f1f1f1" stroke-width="1.2"/>
    </svg>
    <div class="divider"></div>

    <div class="contact">
      <div class="person">Miriam Holloway</div>
      <div class="company">Veritrace Kilonga</div>
      <div class="address">
        <div class="line">PO Box 48317</div>
        <div class="line">Arusha, Tanzania</div>
      </div>
      <div class="reach">
        <div class="line">+255 612 839 274</div>
        <div class="line">miriamholloway@postvale.example</div>
        <div class="line">www.miriamholloway.example</div>
      </div>
    </div>
  </section>
</div>
</body>
</html>
```